Certificates with Watermark Images

We are looking for a design of One page Certificates with Watermark (background) images where text will be printed over it .
Graphics design is required to reflect the flowing categories:
IPTV (Internet Protocol TV)
VoD (Video on Demand)
Satellite Receiver
Graphics design images for all three categories must be provided to maintain the same them .
Thank you and good luck.
Industry/Entity Type
Internet
Requirements
Must have
- Graphics design images for all three categories must be provided to maintain the same them

```html
<!DOCTYPE html>
<html lang="en">
<head>
<meta charset="utf-8">
<title>Certificate – Bright Horizon</title>
<link href="https://fonts.googleapis.com/css2?family=Fira+Sans:ital,wght@0,400;0,500;0,700;1,700&display=swap" rel="stylesheet">
<style>
  :root {
    --page-bg: #ffffff;
    --frame-edge: #d9dde2;
    --ink: #2b2b2b;
    --ink-soft: #3a3a3a;
    --accent-blue: #1d9be3;
    --brand-orange: #ef5a2a;
    --seal-blue: #2a13a8;
    --wash: #f4f5f6;
    --haze: #dfe3e7;
    --screen-grey: #a3a6aa;
    --screen-edge: #7c8188;
    --panel-blue: #9fb6cc;
    --panel-deep: #6f8296;
  }
  * { box-sizing: border-box; margin: 0; padding: 0; }
  html, body {
    width: 1200px; height: 845px; overflow: hidden;
    background: var(--page-bg);
    font-family: "Fira Sans", Arial, sans-serif;
    color: var(--ink);
  }
  .certificate {
    position: absolute; left: 28px; top: 26px;
    width: 1144px; height: 790px;
    border-radius: 44px;
    border: 2px solid var(--frame-edge);
    overflow: hidden;
  }
  .backdrop {
    position: absolute; inset: 0;
    background:
      radial-gradient(ellipse 230px 210px at 72% 40%, rgba(255,255,255,0.55), transparent 75%),
      radial-gradient(ellipse 330px 260px at 72% 40%, var(--screen-grey) 0%, rgba(163,166,170,0.85) 55%, transparent 100%),
      linear-gradient(180deg, rgba(111,130,150,0.35) 0%, transparent 18%, transparent 72%, rgba(111,130,150,0.4) 100%),
      linear-gradient(90deg, var(--haze) 0%, var(--wash) 10%, var(--wash) 34%, var(--haze) 46%, #cfd5db 62%, var(--panel-blue) 90%, var(--panel-deep) 100%);
  }
  .content { position: absolute; left: 0; top: 0; width: 640px; height: 100%; text-align: center; }
  .content > * { position: absolute; left: 0; width: 628px; }
  .brand-dot {
    left: 282px; width: 64px; top: 56px; height: 64px; border-radius: 50%;
    background: var(--brand-orange);
  }
  .brand-name { top: 139px; font-size: 25px; line-height: 30px; font-weight: 700; color: var(--ink-soft); }
  .title { top: 215px; font-size: 44px; line-height: 53px; font-weight: 700; letter-spacing: 7px; color: var(--ink); }
  .intro { top: 283px; font-size: 20px; line-height: 24px; }
  .recipient { top: 315px; font-size: 40px; line-height: 48px; font-weight: 700; color: var(--accent-blue); }
  .service { top: 379px; font-size: 18px; line-height: 22px; }
  .citation { top: 424px; font-size: 18px; line-height: 25px; }
  .award { top: 535px; font-size: 18px; line-height: 22px; font-weight: 700; }
  .content > .meta {
    left: 77px; width: 260px; font-size: 13px; font-weight: 700; font-style: italic;
    line-height: 18px; color: var(--ink-soft); text-align: left;
  }
  .meta-number { top: 636px; }
  .meta-place { top: 672px; }
  .meta-signatory { top: 722px; }
  .content > .signature-area {
    left: 282px; top: 646px; width: 110px; height: 78px;
    border-radius: 20px;
    background: linear-gradient(135deg, rgba(42,19,168,0.10), rgba(42,19,168,0.03));
  }
  .content > .seal { left: 466px; top: 617px; width: 134px; height: 134px; }
</style>
</head>
<body>
  <main class="certificate">
    <div class="backdrop" role="img" aria-label="Faded photo of a wall of glowing TV screens around a large grey screen showing an at sign, for IPTV and satellite service"></div>
    <section class="content">
      <span class="brand-dot"></span>
      <p class="brand-name">Our Organization</p>
      <h1 class="title">CERTIFICATE</h1>
      <p class="intro">this certificate that</p>
      <h2 class="recipient">Bright Horizon</h2>
      <p class="service">(satellite service)</p>
      <p class="citation">has been awarded for his labor achievements<br>and many years of diligent work, also for his<br>labor achievements and many years of diligent<br>work.</p>
      <p class="award">and has passed for this Certificate $100</p>
      <p class="meta meta-number">Certificate No. 0000/1</p>
      <p class="meta meta-place">11 November 2011<br>New-York</p>
      <p class="meta meta-signatory">Our company Genera Director<br>Samir Haddad</p>
      <div class="signature-area" role="img" aria-label="Handwritten director signature"></div>
      <svg class="seal" viewBox="0 0 134 134" aria-hidden="true">
        <polygon fill="var(--seal-blue)" points="67,2 74,14 85,5 89,18 102,12 102,26 116,24 112,37 126,40 118,51 130,58 120,67 130,76 118,83 126,94 112,97 116,110 102,108 102,122 89,116 85,129 74,120 67,132 60,120 49,129 45,116 32,122 32,108 18,110 22,97 8,94 16,83 4,76 14,67 4,58 16,51 8,40 22,37 18,24 32,26 32,12 45,18 49,5 60,14"/>
      </svg>
    </section>
  </main>
</body>
</html>
```